Business Cards for a law firm

Business cards for our law firm. Use our silhoette logo and OAK PARTNERS - check our website (www.oakpartners.example)

Contact Information for Business Card

our silhouette logo, OAK PARTNERS, 800-555-0147, Dorian Pemberton, dorian@oakpartners.example

Requirements
Must have
• our silhouette logo, OAK PARTNERS, 800-555-0147, Dorian Pemberton, dorian@oakpartners.example

```html
<!DOCTYPE html>
<html lang="en">
<head>
<meta charset="utf-8">
<title>Oak Partners – Business Cards</title>
<link href="https://fonts.googleapis.com/css2?family=Montserrat:wght@400;500;700;800&display=swap" rel="stylesheet">
<style>
  :root {
    --stage: #1c1c1e;
    --navy: #2e3a6b;
    --navy-deep: #232d57;
    --navy-light: #4a5688;
    --orange: #f7a823;
    --white: #ffffff;
    --suit: #262c44;
  }
  * { box-sizing: border-box; margin: 0; padding: 0; }
  html, body { width: 1200px; height: 969px; overflow: hidden; }
  body {
    background: var(--stage);
    font-family: "Montserrat", Arial, sans-serif;
    color: var(--white);
    position: relative;
  }
  .card {
    position: absolute;
    left: 240px;
    width: 720px;
    height: 411px;
    overflow: hidden;
    background: var(--navy);
    box-shadow: 0 10px 30px rgba(0,0,0,.5);
  }
  .card--contact { top: 48px; }
  .card--promo { top: 506px; }

  .office-photo {
    position: absolute; inset: 0;
    background: linear-gradient(160deg, var(--navy-deep) 0%, var(--navy) 45%, var(--navy-light) 75%, var(--navy) 100%);
    opacity: .9;
  }

  .brand {
    position: absolute;
    display: flex; align-items: center; gap: 12px;
    left: 50%; transform: translateX(-50%);
    white-space: nowrap;
  }
  .brand__mark {
    width: 40px; height: 40px; border-radius: 50%;
    background: var(--white);
  }
  .brand__name {
    font-weight: 800; font-size: 30px; letter-spacing: 2px; color: var(--white);
  }

  .card--contact .brand { top: 78px; }
  .contact {
    position: absolute; top: 150px; left: 0; right: 0;
    text-align: center;
  }
  .contact__name {
    font-weight: 800; font-size: 27px; letter-spacing: 1.5px; text-transform: uppercase;
    margin-bottom: 10px;
  }
  .contact__icon { display: block; margin: 0 auto 3px; width: 18px; height: 14px; }
  .contact__line { font-size: 20px; font-weight: 500; margin-bottom: 8px; letter-spacing: .5px; }

  .card--promo .brand { top: 22px; }
  .card--promo .brand__name { font-size: 26px; }
  .card--promo .brand__mark { width: 34px; height: 34px; }

  .person {
    position: absolute; bottom: 0;
    background: linear-gradient(180deg, #6b5a52 0%, #6b5a52 28%, var(--white) 28%, var(--white) 36%, var(--suit) 36%, #1d2238 100%);
    border-radius: 46% 46% 0 0 / 30% 30% 0 0;
  }
  .person--left { left: 40px; width: 210px; height: 250px; }
  .person--right { right: 30px; width: 200px; height: 300px; bottom: 40px; }

  .pitch {
    position: absolute; top: 80px; left: 230px; width: 270px;
    text-align: center;
  }
  .pitch__firm { color: var(--orange); font-weight: 800; font-size: 20px; letter-spacing: .5px; }
  .pitch__headline { font-weight: 800; font-size: 20px; line-height: 1.25; margin-top: 4px; text-transform: uppercase; }
  .pitch__stat { font-size: 15px; font-weight: 500; line-height: 1.3; margin-top: 8px; }
  .pitch__button {
    display: inline-block; margin-top: 12px;
    background: var(--orange); color: var(--navy-deep);
    font-weight: 800; font-size: 12.5px; letter-spacing: .3px;
    padding: 11px 18px; border-radius: 24px; white-space: nowrap;
  }

  .band { position: absolute; left: 0; bottom: 0; width: 720px; height: 76px; }
  .band__label {
    position: absolute; color: var(--navy-deep); font-weight: 500; white-space: nowrap;
    display: flex; align-items: center; gap: 8px;
  }
  .band__label--consult { left: 18px; bottom: 8px; font-size: 15px; }
  .band__label--fee { left: 240px; width: 300px; justify-content: center; bottom: 18px; font-size: 19px; }
  .band__label--visit { right: 14px; bottom: 10px; font-size: 13.5px; }
  .band__dot { width: 26px; height: 26px; border-radius: 50%; background: var(--navy); border: 2px solid var(--white); }
</style>
</head>
<body>

<section class="card card--contact">
  <div class="office-photo" role="img" aria-label="Photo of the firm's modern glass office interior, tinted navy"></div>
  <div class="brand">
    <span class="brand__mark"></span>
    <span class="brand__name">OAK PARTNERS</span>
  </div>
  <div class="contact">
    <p class="contact__name">Dorian Pemberton</p>
    <svg class="contact__icon" viewBox="0 0 18 14" aria-hidden="true">
      <path d="M2 5 Q9 0 16 5 L14 7 L12 5 L6 5 L4 7 Z M5 7 H13 L15 13 H3 Z" fill="#fff"/>
    </svg>
    <p class="contact__line">800-555-0147</p>
    <svg class="contact__icon" viewBox="0 0 18 14" aria-hidden="true">
      <rect x="1" y="1" width="16" height="12" fill="#fff"/>
      <path d="M1 1 L9 8 L17 1" stroke="#2e3a6b" stroke-width="1.5" fill="none"/>
    </svg>
    <p class="contact__line">dorian@oakpartners.example</p>
    <svg class="contact__icon" viewBox="0 0 18 14" aria-hidden="true">
      <circle cx="9" cy="7" r="6.5" fill="#fff"/>
      <path d="M2.5 7 H15.5 M9 .5 V13.5 M9 .5 Q4 7 9 13.5 M9 .5 Q14 7 9 13.5" stroke="#2e3a6b" stroke-width="1" fill="none"/>
    </svg>
    <p class="contact__line">www.oakpartners.example</p>
  </div>
</section>

<section class="card card--promo">
  <div class="office-photo" role="img" aria-label="Photo of the firm's office interior, tinted navy"></div>
  <div class="brand">
    <span class="brand__mark"></span>
    <span class="brand__name">OAK PARTNERS</span>
  </div>

  <div class="person person--left" role="img" aria-label="Portrait photo of a smiling attorney in a dark suit and plaid tie"></div>
  <div class="person person--right" role="img" aria-label="Portrait photo of a smiling attorney in a navy suit and dark tie"></div>

  <div class="pitch">
    <p class="pitch__firm">OAK PARTNERS</p>
    <p class="pitch__headline">Injured?<br>Call Oak<br>Partners!</p>
    <p class="pitch__stat">Over $400,000,000<br>Recovered For Our Clients.</p>
    <span class="pitch__button">GET A FREE CONSULTATION NOW</span>
  </div>

  <svg class="band" viewBox="0 0 720 76" aria-hidden="true">
    <polygon points="0,42 210,42 204,76 0,76" fill="#f7a823"/>
    <polygon points="210,76 222,10 548,10 562,76" fill="#f7a823"/>
    <polygon points="562,36 720,36 720,76 571,76" fill="#f7a823"/>
  </svg>
  <span class="band__label band__label--consult">
    <svg width="18" height="18" viewBox="0 0 18 18" aria-hidden="true"><rect x="1" y="1" width="11" height="8" rx="2" fill="none" stroke="#232d57" stroke-width="1.5"/><circle cx="5" cy="14" r="2.5" fill="none" stroke="#232d57" stroke-width="1.5"/><circle cx="13" cy="14" r="2.5" fill="none" stroke="#232d57" stroke-width="1.5"/></svg>
    Free Consultation
  </span>
  <span class="band__label band__label--fee"><span class="band__dot"></span>No Fee Unless You Win</span>
  <span class="band__label band__label--visit">
    <svg width="18" height="18" viewBox="0 0 18 18" aria-hidden="true"><circle cx="9" cy="9" r="8.5" fill="#2e3a6b"/><path d="M9 4 a3 3 0 0 1 3 3 c0 2.5 -3 6 -3 6 s-3 -3.5 -3 -6 a3 3 0 0 1 3 -3z" fill="#f7a823"/></svg>
    We'll Come To You
  </span>
</section>

</body>
</html>
```